Bluefinch Painting needs a Website

We need a website built for a Painting company I own, we mainly do residential painting, but don't want to be limited to that.

Need to have estimate request form.
Need pic's of past projects

I like the look of the website for http://www.harbor-brushworks.com
& "Westlake Home inspections"

My logo that was designed here on ArtHatch on the front page

I would like one of the houses I downloaded as part of the background
of the front page.

Target Market(s)

Home owners

Industry/Entity Type

Painting

Number of Pages Required

1 page

Font styles to use
Serif

Requirements
Must have
• Estimate request form for home owners to fill out -
• Name:
• Phone Number:
• Address:
• E-mail:
• Painting project description:
• And my info to:
• My phone number: (555) 318-7046
• My web address bluefinchpainting.example
Nice to have
• My logo that was designed here on ArtHatch

```html
<!DOCTYPE html>
<html lang="en">
<head>
<meta charset="utf-8">
<title>Bluefinch Painting</title>
<link rel="stylesheet" href="https://fonts.googleapis.com/css2?family=Crimson+Text:wght@400;600&family=Arimo:wght@400;700&family=Roboto+Condensed:wght@400&display=swap">
<style>
:root{
  --blue:#1b7fcc;
  --blue-dark:#1469ad;
  --ink:#1a1a1a;
  --text:#333;
  --white:#fff;
  --sky:#b8d8ea;
  --band:#f2f2f2;
  --black:#0c0c0c;
  --charcoal:#2e2e2e;
  --field:#e6e4e1;
}
*{margin:0;padding:0;box-sizing:border-box}
html,body{width:1200px;height:975px;overflow:hidden;background:var(--white)}
body{position:relative;font-family:"Arimo",Arial,sans-serif;color:var(--text)}
.abs{position:absolute}

/* header */
.site-header{left:0;top:0;width:1200px;height:116px;background:var(--white)}
.brand{left:160px;top:48px;display:flex;align-items:center;gap:10px;font-family:"Crimson Text",Georgia,serif;font-weight:600;font-size:33px;color:var(--ink);letter-spacing:.5px}
.brand-square{width:34px;height:34px;background:var(--blue)}
.estimate-btn{left:719px;top:17px;width:150px;height:28px;background:var(--blue);color:var(--white);font-family:"Roboto Condensed",Arial,sans-serif;font-size:18px;display:flex;align-items:center;justify-content:center;border-radius:2px}
.call{left:884px;top:16px;display:flex;gap:8px;align-items:flex-start}
.call svg{margin-top:1px}
.call-label{font-size:14px;color:#333;line-height:17px}
.call-number{font-size:20px;color:#333;line-height:24px}
.main-nav{left:590px;top:71px;display:flex;align-items:center;font-size:13px;color:#222;height:23px}
.main-nav a{color:inherit;text-decoration:none}
.nav-home{left:590px;top:71px;width:64px;height:23px;background:var(--blue);color:var(--white)!important;display:flex;align-items:center;justify-content:center}
.nav-item{top:75px;font-size:13px;color:#222;text-decoration:none}

/* hero */
.hero{left:0;top:116px;width:1200px;height:397px;background:linear-gradient(90deg,#5a2410 0%,#9a3a18 22%,#b8622a 45%,#c99a5c 62%,#e4cfa8 80%,#efe4cc 100%)}
.hero-shade{left:0;top:116px;width:1200px;height:397px;background:linear-gradient(180deg,rgba(0,0,0,0) 55%,rgba(40,20,10,.35) 100%)}
.headline{left:230px;top:182px;width:496px;text-align:center;font-family:"Crimson Text",Georgia,serif;font-size:32px;line-height:43px;color:#1c120c;letter-spacing:.5px;text-shadow:0 1px 3px rgba(255,230,200,.55)}
.arrow{width:41px;height:35px;background:rgba(210,210,210,.75);display:flex;align-items:center}
.arrow span{width:28px;height:28px;background:#2d2d2d;display:flex;align-items:center;justify-content:center}
.arrow-left{left:0;top:293px;justify-content:flex-end;padding-right:4px}
.arrow-right{left:1154px;top:293px;width:46px;padding-left:4px}

.quote-panel{left:751px;top:183px;width:291px;height:329px;background:rgba(85,70,60,.72)}
.quote-title{left:806px;top:210px;display:flex;align-items:center;font-family:"Crimson Text",Georgia,serif;font-size:23px;color:var(--white);font-weight:600}
.quote-title .free{background:var(--blue);padding:0 3px;margin-right:4px;line-height:34px}
.field{left:769px;width:264px;height:30px;background:var(--field);border-radius:3px;font-size:12.5px;color:#444;padding:8px 12px;box-shadow:inset 0 1px 2px rgba(0,0,0,.15)}
.field-desc{height:77px}
.submit-line{left:777px;top:486px;width:248px;height:1px;background:var(--white)}
.submit-bars{top:481px;width:22px;height:11px;border-top:1px solid var(--white);border-bottom:1px solid var(--white)}
.submit-bars::after{content:"";position:absolute;left:0;top:4px;width:22px;height:1px;background:var(--white)}
.submit-btn{left:870px;top:472px;width:63px;height:26px;background:var(--black);color:var(--white);font-weight:700;font-size:14px;display:flex;align-items:center;justify-content:center;border-radius:2px}

.tab{top:467px;height:46px;display:flex;align-items:center;padding-left:12px;font-family:"Crimson Text",Georgia,serif;font-size:21px;color:var(--white)}
.tab-residential{left:160px;width:246px;background:var(--blue);font-weight:600}
.tab-commercial{left:432px;width:246px;background:var(--charcoal);padding-left:8px}

/* gallery */
.gallery{left:160px;top:513px;width:882px;height:177px;background:linear-gradient(180deg,#e8e8e8 0%,#f6f6f6 40%,#f3f3f3 100%)}
.thumb{top:547px;width:154px;height:124px;border:1px solid #444;background:var(--white);padding:4px}
.thumb-photo{position:relative;width:100%;height:100%;box-shadow:0 0 0 1px #999}
.thumb-caption{position:absolute;left:7px;bottom:4px;font-family:"Crimson Text",Georgia,serif;font-size:17px;color:var(--white);text-shadow:0 1px 2px rgba(0,0,0,.8)}

/* welcome */
.welcome{left:0;top:690px;width:1200px;height:215px;background:var(--sky)}
.welcome-title{left:0;top:713px;width:1200px;text-align:center;font-family:"Crimson Text",Georgia,serif;font-size:23px;color:#1d2a3a}
.welcome-copy{left:176px;top:775px;width:848px;text-align:center;font-size:12.5px;line-height:22px;color:#2d3c48}
.readmore-line{left:477px;top:868px;width:247px;height:1px;background:var(--white)}
.readmore-bars{top:863px;width:22px;height:11px;border-top:1px solid var(--white);border-bottom:1px solid var(--white)}
.readmore-bars::after{content:"";position:absolute;left:0;top:4px;width:22px;height:1px;background:var(--white)}
.readmore-btn{left:561px;top:856px;width:78px;height:24px;background:var(--black);color:var(--white);font-size:13px;display:flex;align-items:center;justify-content:center;border-radius:2px}

/* footer */
.site-footer{left:0;top:905px;width:1200px;height:65px;background:var(--black)}
.footer-bar{left:0;top:970px;width:1200px;height:5px;background:var(--blue-dark)}
.footer-nav{left:165px;top:917px;display:flex;gap:0;font-size:13px;color:var(--white)}
.footer-nav span{margin-right:19px}
.copyright{left:162px;top:940px;font-size:12px;color:var(--white)}
.footer-brand{left:858px;top:926px;display:flex;align-items:center;gap:8px;font-family:"Crimson Text",Georgia,serif;font-weight:600;font-size:22px;color:#d8d8d8}
.footer-brand .brand-square{width:22px;height:22px;background:#d8d8d8}
</style>
</head>
<body>

<header class="site-header abs"></header>
<div class="brand abs"><span class="brand-square"></span>Bluefinch Painting</div>
<div class="estimate-btn abs">Free Estimates</div>
<div class="call abs">
  <svg width="28" height="28" viewBox="0 0 28 28" aria-hidden="true"><circle cx="14" cy="14" r="13" fill="none" stroke="#1b7fcc" stroke-width="1.6"/><path d="M10 7c-2 1-3 3-2 6 1 4 4 7 7 8 2 1 4 0 5-2l-3-2-2 1c-2-1-3-3-4-5l1-2z" fill="#1b7fcc"/></svg>
  <div><div class="call-label">Call Us Today</div><div class="call-number">555-318-7046</div></div>
</div>
<nav>
  <a class="nav-home abs" style="font-size:13px;text-decoration:none">HOME</a>
  <a class="nav-item abs" style="left:674px">ABOUT US</a>
  <a class="nav-item abs" style="left:756px;top:76px">SERVICES</a>
  <a class="nav-item abs" style="left:840px;top:77px">PAST PROJECTS</a>
  <a class="nav-item abs" style="left:961px;top:76px">CONTACT US</a>
</nav>

<div class="hero abs" role="img" aria-label="Freshly painted bedroom with warm orange walls, a large bed with pillows and a bright bathroom beyond"></div>
<div class="hero-shade abs"></div>
<h1 class="headline abs" style="font-weight:400">PROVIDING QUALITY WORK AT AFFORDABLE PRICES</h1>
<div class="arrow arrow-left abs"><span><svg width="10" height="12" viewBox="0 0 10 12"><path d="M7 1 2 6l5 5" fill="none" stroke="#fff" stroke-width="2.4"/></svg></span></div>
<div class="arrow arrow-right abs"><span><svg width="10" height="12" viewBox="0 0 10 12"><path d="M3 1l5 5-5 5" fill="none" stroke="#fff" stroke-width="2.4"/></svg></span></div>

<form class="quote-form">
  <div class="quote-panel abs"></div>
  <div class="quote-title abs"><span class="free">Free</span>PAINTING Estimates</div>
  <div class="field abs" style="top:252px">Name</div>
  <div class="field abs" style="top:297px">Email</div>
  <div class="field abs" style="top:338px">Phone</div>
  <div class="field field-desc abs" style="top:377px">Painting project description</div>
  <div class="submit-line abs"></div>
  <div class="submit-bars abs" style="left:846px"></div>
  <div class="submit-bars abs" style="left:933px"></div>
  <div class="submit-btn abs">Submit</div>
</form>

<div class="tab tab-residential abs">RESIDENTIAL PAINTING</div>
<div class="tab tab-commercial abs">COMMERCIAL PAINTING</div>

<section class="gallery abs"></section>
<div class="thumb abs" style="left:175px"><div class="thumb-photo" role="img" aria-label="Painted living room with wooden staircase" style="background:linear-gradient(180deg,#d9c9a8,#a8764a 70%,#6b3f22)"><span class="thumb-caption">Lorem Ispum</span></div></div>
<div class="thumb abs" style="left:348px"><div class="thumb-photo" role="img" aria-label="House exterior with grey siding being painted" style="background:linear-gradient(160deg,#2a6fb8 0%,#8a97a6 45%,#c7ccd2 100%)"><span class="thumb-caption">Lorem Ispum</span></div></div>
<div class="thumb abs" style="left:520px"><div class="thumb-photo" role="img" aria-label="Yellow painted hallway with white stairs" style="background:linear-gradient(180deg,#e5c45a,#c49a3a 60%,#8a5a2a)"><span class="thumb-caption">Lorem Ispum</span></div></div>
<div class="thumb abs" style="left:693px"><div class="thumb-photo" role="img" aria-label="Painted two storey family home with lawn" style="background:linear-gradient(180deg,#cfe0ee 0%,#b8a590 45%,#5f8a3a 75%,#4a7a2a 100%)"><span class="thumb-caption">Lorem Ispum</span></div></div>
<div class="thumb abs" style="left:865px"><div class="thumb-photo" role="img" aria-label="Bright entry hall with painted staircase" style="background:linear-gradient(180deg,#f1ede4,#cbb89a 65%,#8c7458)"><span class="thumb-caption">Lorem Ispum</span></div></div>

<section class="welcome abs"></section>
<h2 class="welcome-title abs" style="font-weight:400">Welcome to Bluefinch Painting</h2>
<svg class="abs" style="left:437px;top:746px" width="346" height="14" viewBox="0 0 346 14" aria-hidden="true">
  <line x1="0" y1="5" x2="346" y2="5" stroke="#1d2a3a" stroke-width="1"/>
  <line x1="0" y1="8" x2="346" y2="8" stroke="#1d2a3a" stroke-width="1"/>
  <path d="M167 1l12 12M179 1l-12 12" stroke="#1d2a3a" stroke-width="1.2"/>
</svg>
<p class="welcome-copy abs">Lorem ipsum dolor sit amet, consectetuer adipiscing elit, sed diam nonummy nibh euismod&nbsp; rent ut laoreet dolore magna aliquam erat volutpat. Ut wisi enim ad minim veniam, quis nostrud lore xererci tation ullamcorper suscipit lobortis nisl ut aliquip ex ea commodo consequat. Duis autem revel eum iriure dolor in hendrerit in vulputate velit esse molestie consequat.</p>
<div class="readmore-line abs"></div>
<div class="readmore-bars abs" style="left:539px"></div>
<div class="readmore-bars abs" style="left:639px"></div>
<div class="readmore-btn abs">Read More</div>

<footer class="site-footer abs"></footer>
<div class="footer-nav abs"><span>• Home</span><span>• About Us</span><span>• Services</span><span>• &nbsp;Past Projects</span><span>• Contact Us</span></div>
<div class="copyright abs">Copyright ©2015, BluefinchPainting&nbsp; All Rights Reserved</div>
<div class="footer-brand abs"><span class="brand-square"></span>Bluefinch Painting</div>
<div class="footer-bar abs"></div>

</body>
</html>
```